Unique Business Card Design

Unique Business Card design for our orthotic and prosthetic company. Our logo is on our website, color is light blue. Unique shape (artificial leg shaped, vertical, etc..) preferred. Logo, business name, individual name and basic demographics needed.

Industry/Entity Type

Business

Contact Information for Business Card

Logo, Industry, Phone # Logo, "Prosthetic & Orthotic Services" Place to add individual name and contact info

Colors
cee9f5

Requirements
Must have
• The icon must be there, placement of "Prosthetic & Orthotic Services" can be moved
Nice to have
• Like the mix of light blue, and a little darker blue. One design included the icons from my website which was a nice touch

```html
<!DOCTYPE html>
<html lang="en">
<head>
<meta charset="utf-8">
<title>Stridefrom Inc. — Business Card</title>
<link href="https://fonts.googleapis.com/css2?family=Open+Sans:ital,wght@0,400;0,600;0,700;1,400&family=Crimson+Text:ital@1&display=swap" rel="stylesheet">
<style>
  :root {
    --brand-blue: #1560ab;
    --text-grey: #555a60;
    --card-white: #ffffff;
    --page-bg: #e6e9ed;
  }
  * { margin: 0; padding: 0; box-sizing: border-box; }
  html, body {
    width: 1105px; height: 1200px; overflow: hidden;
    background: var(--page-bg);
    font-family: "Open Sans", Arial, sans-serif;
  }
  .canvas { position: relative; width: 1105px; height: 1200px; }
  .card {
    position: absolute; left: 193px; width: 720px; height: 410px;
    border-radius: 22px;
  }
  .card--front { top: 167px; background: var(--card-white); }
  .card--back { top: 623px; background: var(--brand-blue); }

  .brand-dot {
    position: absolute; left: 41px; top: 45px; width: 86px; height: 86px;
    border-radius: 50%; background: var(--brand-blue);
  }
  .brand-name {
    position: absolute; left: 149px; top: 54px;
    font-size: 23px; font-weight: 600; color: var(--brand-blue); letter-spacing: 0.2px;
  }
  .brand-rule {
    position: absolute; left: 149px; top: 88px; width: 529px; height: 2px;
    background: var(--brand-blue);
  }
  .brand-tagline {
    position: absolute; left: 160px; top: 91px;
    font-family: "Crimson Text", Georgia, serif; font-style: italic;
    font-size: 15px; color: var(--brand-blue);
  }
  .person { position: absolute; right: 42px; top: 56px; text-align: right; color: var(--brand-blue); }
  .person-name { font-size: 25px; font-weight: 600; line-height: 30px; }
  .person-title { font-size: 18px; font-weight: 700; line-height: 24px; margin-top: 4px; }

  .contact-list { position: absolute; left: 44px; top: 272px; list-style: none; }
  .contact-item {
    display: flex; align-items: center; height: 27.7px;
    font-size: 18px; color: var(--text-grey);
  }
  .contact-icon { width: 18px; height: 18px; margin-right: 8px; fill: var(--brand-blue); }

  .address {
    position: absolute; right: 42px; top: 307px; text-align: right;
    font-size: 18px; line-height: 25.5px; color: var(--text-grey); font-style: normal;
  }

  .back-mark {
    position: absolute; left: 246px; top: 98px; width: 226px; height: 220px;
    border-radius: 50%; background: var(--card-white);
    display: flex; align-items: center; justify-content: center;
  }
  .back-mark-name { font-size: 23px; font-weight: 600; color: var(--brand-blue); }
  .back-web {
    position: absolute; left: 0; right: 0; top: 341px; text-align: center;
    font-size: 19px; font-style: italic; letter-spacing: 4.5px; color: var(--card-white);
  }
</style>
</head>
<body>
<main class="canvas">
  <section class="card card--front" aria-label="Card front">
    <div class="brand-dot"></div>
    <div class="brand-name">STRIDEFORM INC.</div>
    <div class="brand-rule"></div>
    <div class="brand-tagline">Prosthetic &amp; Orthotic Services</div>

    <div class="person">
      <div class="person-name">Miriam Castell</div>
      <div class="person-title">CO LPO</div>
    </div>

    <ul class="contact-list">
      <li class="contact-item">
        <svg class="contact-icon" viewBox="0 0 24 24" aria-hidden="true"><path d="M6.6 10.8c1.4 2.8 3.8 5.1 6.6 6.6l2.2-2.2c.3-.3.7-.4 1-.2 1.1.4 2.3.6 3.6.6.6 0 1 .4 1 1V20c0 .6-.4 1-1 1C10.6 21 3 13.4 3 4c0-.6.4-1 1-1h3.5c.6 0 1 .4 1 1 0 1.3.2 2.5.6 3.6.1.3 0 .7-.2 1l-2.3 2.2z"/></svg>
        555.014.2200
      </li>
      <li class="contact-item">
        <svg class="contact-icon" viewBox="0 0 24 24" aria-hidden="true"><path d="M7 1h10c1.1 0 2 .9 2 2v18c0 1.1-.9 2-2 2H7c-1.1 0-2-.9-2-2V3c0-1.1.9-2 2-2zm0 3v14h10V4H7zm5 15.5a1.2 1.2 0 1 0 0 2.4 1.2 1.2 0 0 0 0-2.4z"/></svg>
        555.014.3810
      </li>
      <li class="contact-item">
        <svg class="contact-icon" viewBox="0 0 24 24" aria-hidden="true"><path d="M6 2h12v5H6zM3 8h18c1.1 0 2 .9 2 2v7h-4v5H5v-5H1v-7c0-1.1.9-2 2-2zm4 8v4h10v-4H7z"/></svg>
        555-0147726
      </li>
      <li class="contact-item">
        <svg class="contact-icon" viewBox="0 0 24 24" aria-hidden="true"><path d="M2 5h20v14H2V5zm2 2v.4l8 5.2 8-5.2V7H4z"/></svg>
        mcastell@strideforminc.com
      </li>
    </ul>

    <address class="address">
      820 Harbor Ave.<br>
      Millbrook, NY 10550<br>
      www.strideforminc.com
    </address>
  </section>

  <section class="card card--back" aria-label="Card back">
    <div class="back-mark"><span class="back-mark-name">STRIDEFORM</span></div>
    <div class="back-web">www.strideforminc.com</div>
  </section>
</main>
</body>
</html>
```